Newsletter Ad

I am looking for someone to design an advertisement for a mother's club newsletter. 4" wide X by 5" tall (and 2.5" wide X 5" tall if possible).

I'm a psychotherapist, so want the ad to look professional, but modern. I have a logo with my photo attached that can be incorporated into the design. The colors of my website are turquoise and white. I'd like to keep with that theme...so maybe some turquoise blocking to match the logo font color.

I'm uploading a logo as well as an ad draft with the content I'd like listed in the ad.

```html
<!DOCTYPE html>
<html lang="en">
<head>
<meta charset="utf-8">
<title>Dana Morrow, MA, MFT – Psychotherapy Ad</title>
<link rel="stylesheet" href="https://fonts.googleapis.com/css2?family=Didact+Gothic&display=swap">
<style>
  :root {
    --teal: #3a9a97;
    --teal-text: #3b9895;
    --ink: #2b2b2b;
    --rule: #4a4a4a;
    --paper: #ffffff;
    --portrait-light: #d9b49a;
    --portrait-mid: #8a5e44;
    --portrait-dark: #2c211d;
  }
  html, body {
    margin: 0;
    padding: 0;
    width: 1200px;
    height: 2400px;
    overflow: hidden;
    background: var(--paper);
  }
  .ad {
    position: relative;
    width: 1200px;
    height: 2400px;
    background: var(--paper);
    font-family: "Didact Gothic", "Century Gothic", sans-serif;
    color: var(--ink);
  }
  .portrait {
    position: absolute;
    left: 400px;
    top: 0;
    width: 400px;
    height: 373px;
    background: radial-gradient(ellipse at 50% 35%, var(--portrait-light) 0%, var(--portrait-mid) 45%, var(--portrait-dark) 100%);
    border-radius: 46% 46% 0 0 / 40% 40% 0 0;
  }
  .rule {
    position: absolute;
    left: 40px;
    width: 1120px;
    height: 5px;
    background: var(--rule);
  }
  .rule--top { top: 371px; }
  .rule--bottom { top: 510px; }
  .therapist-name {
    position: absolute;
    top: 382px;
    left: 0;
    width: 100%;
    margin: 0;
    text-align: center;
    font-weight: 400;
    font-size: 100px;
    line-height: 120px;
    color: var(--teal-text);
    letter-spacing: -1px;
  }
  .service {
    position: absolute;
    top: 555px;
    left: 0;
    width: 100%;
    margin: 0;
    text-align: center;
    font-weight: 400;
    font-size: 92px;
    line-height: 110px;
  }
  .service__for { font-size: 58px; }
  .clients {
    position: absolute;
    top: 690px;
    left: 0;
    width: 100%;
    margin: 0;
    text-align: center;
    font-size: 58px;
    line-height: 70px;
  }
  .specialties {
    position: absolute;
    top: 805px;
    left: 0;
    width: 100%;
    height: 1056px;
    background: var(--teal);
    margin: 0;
    padding: 36px 0 0;
    box-sizing: border-box;
    list-style: none;
    text-align: center;
  }
  .specialties li {
    color: var(--paper);
    font-size: 76px;
    line-height: 120px;
  }
  .contact {
    position: absolute;
    top: 1920px;
    left: 0;
    width: 100%;
    margin: 0;
    text-align: center;
    font-style: normal;
    font-size: 54px;
    line-height: 61px;
  }
  .license-band {
    position: absolute;
    top: 2229px;
    left: 0;
    width: 100%;
    height: 171px;
    background: var(--teal);
  }
  .license {
    position: absolute;
    right: 52px;
    top: 52px;
    margin: 0;
    color: var(--paper);
    font-size: 43px;
    line-height: 60px;
  }
</style>
</head>
<body>
  <div class="ad">
    <div class="portrait" role="img" aria-label="Portrait photo of the therapist"></div>
    <div class="rule rule--top"></div>
    <h1 class="therapist-name">DANA MORROW, MA, MFT</h1>
    <div class="rule rule--bottom"></div>
    <p class="service">Psychotherapy <span class="service__for">for</span></p>
    <p class="clients">Individuals, Couples and Families</p>
    <ul class="specialties">
      <li>Parenting</li>
      <li>Depression</li>
      <li>Anxiety</li>
      <li>Life Transitions</li>
      <li>Divorce</li>
      <li>Couples Issues</li>
      <li>Women’s Issues</li>
      <li>Attachment and Neuroscience</li>
    </ul>
    <address class="contact">
      418 Harbor Lane, Bayview, CA 94000<br>
      www.danamorrow.com<br>
      dana@danamorrow.com<br>
      415.555.0186
    </address>
    <div class="license-band">
      <p class="license">License# MFC48210</p>
    </div>
  </div>
</body>
</html>
```